Profesional personal website needs design and business card

I need a business card with my professional name as a logo "Dorian Vitality" for my business. I am a Wellness Coach, consultant and trainer. So it should be professional, wellness oriented and modern.

Target Market(s)

Private clients, governments, corporations. Luxury and high market.

Industry/Entity Type

Health And Wellness

Contact Information for Business Card

Dorian Vitality should be the logo

Colors

Designer to choose colors to be used in the design.

Requirements
Must have
• Dorian Vitality
• Name: Tomás Lirandel
• Wellness Coach, Consultant & Trainer.
• Website: www.dorianvitality-example.com
• Phone:
• Spain (+34) 612 480 317
• (USA) +1 (555) 610 4829
Nice to have
• The most important is the design of "Dorian Vitality", as this is going to be my personal brand logo. It should be professional, wellness, high end and actual.
Should not have
• no golds, no baroque style..

```html
<!DOCTYPE html>
<html lang="en">
<head>
<meta charset="UTF-8">
<title>Dorian Vitality — Business Card</title>
<link href="https://fonts.googleapis.com/css2?family=Roboto:wght@400;500;700&display=swap" rel="stylesheet">
<style>
  :root {
    --ink: #0b0b0b;
    --paper: #ffffff;
    --backdrop: #ecebe8;
    --soft-shadow: rgba(0, 0, 0, 0.12);
  }
  * { margin: 0; padding: 0; box-sizing: border-box; }
  html, body {
    width: 1200px;
    height: 800px;
    overflow: hidden;
    background: var(--backdrop);
    font-family: "Roboto", Arial, sans-serif;
    color: var(--ink);
  }
  .sheet {
    position: relative;
    width: 1200px;
    height: 800px;
  }
  .card {
    position: absolute;
    top: 252px;
    width: 520px;
    height: 297px;
    background: var(--paper);
    box-shadow: 0 10px 30px var(--soft-shadow);
    overflow: hidden;
  }
  .card--front { left: 60px; }
  .card--back { left: 620px; }

  /* Front */
  .brand {
    position: absolute;
    left: 0;
    right: 0;
    text-align: center;
    line-height: 1;
  }
  .card--front .brand { top: 104px; }
  .brand__name {
    font-weight: 700;
    font-size: 35px;
    letter-spacing: 0.2px;
  }
  .brand__tagline {
    margin-top: 4px;
    font-weight: 700;
    font-size: 19px;
  }
  .website {
    position: absolute;
    left: 0;
    right: 0;
    bottom: 34px;
    text-align: center;
    font-size: 16px;
    font-weight: 400;
    letter-spacing: 0.2px;
  }

  /* Back */
  .band {
    position: absolute;
    left: 0;
    right: 0;
    top: 36px;
    height: 92px;
    background: var(--ink);
    color: var(--paper);
  }
  .band .brand { top: 20px; }

  .contact {
    position: absolute;
    left: 0;
    right: 0;
    top: 190px;
    display: flex;
    align-items: center;
    justify-content: center;
    gap: 14px;
  }
  .person { text-align: right; line-height: 1.15; }
  .person__name { font-size: 23px; font-weight: 400; }
  .person__role { font-size: 12.5px; font-weight: 400; }
  .divider {
    width: 1px;
    height: 46px;
    background: var(--ink);
  }
  .phones { list-style: none; font-size: 13px; line-height: 1.5; }
  .phones li { display: flex; align-items: center; gap: 6px; }
  .phone-icon { width: 14px; height: 14px; fill: var(--ink); }
</style>
</head>
<body>
  <main class="sheet">
    <section class="card card--front" aria-label="Business card front">
      <div class="brand">
        <div class="brand__name">Dorian Vitality</div>
        <div class="brand__tagline">Health And Wellness</div>
      </div>
      <div class="website">www.dorianvitality-example.com</div>
    </section>

    <section class="card card--back" aria-label="Business card back">
      <div class="band">
        <div class="brand">
          <div class="brand__name">Dorian Vitality</div>
          <div class="brand__tagline">Health And Wellness</div>
        </div>
      </div>
      <div class="contact">
        <div class="person">
          <div class="person__name">Tomás Lirandel</div>
          <div class="person__role">Wellness Coach, Consultant &amp; Trainer.</div>
        </div>
        <div class="divider"></div>
        <ul class="phones">
          <li>
            <svg class="phone-icon" viewBox="0 0 24 24" aria-hidden="true"><path d="M3 8c0-2 2-4 9-4s9 2 9 4v2h-5V8.5c-1-.5-2.5-.7-4-.7s-3 .2-4 .7V10H3V8zm4 3h10l3 8H4l3-8zm5 2a2.5 2.5 0 1 0 0 5 2.5 2.5 0 0 0 0-5z"/></svg>
            +34 612 480 317 (Spain)
          </li>
          <li>
            <svg class="phone-icon" viewBox="0 0 24 24" aria-hidden="true"><path d="M3 8c0-2 2-4 9-4s9 2 9 4v2h-5V8.5c-1-.5-2.5-.7-4-.7s-3 .2-4 .7V10H3V8zm4 3h10l3 8H4l3-8zm5 2a2.5 2.5 0 1 0 0 5 2.5 2.5 0 0 0 0-5z"/></svg>
            +1 (555) 610 4829 (USA)
          </li>
        </ul>
      </div>
    </section>
  </main>
</body>
</html>
```